Walk Beside The River

Business Card design

Target Market(s)

People who require support in the commnity

Industry/Entity Type

Mental Health Support

Contact Information for Business Card

Mental Health Support Rosalind Tavener walkbesidetheriver@mailcove.com.au 0481 637 092 PO Box 926 Kellerton QLD 4572

Colors
6B429C
8869AF
B7A5CE
E3DAEB
F3F0F8

Requirements
Must have
• Logo & details listed above
Should not have
• No red or orange

```html
<!DOCTYPE html>
<html lang="en">
<head>
<meta charset="utf-8">
<title>Walk Beside The River – Business Card</title>
<link href="https://fonts.googleapis.com/css2?family=Open+Sans:wght@400;600;700;800&display=swap" rel="stylesheet">
<style>
  :root {
    --stage: #232323;
    --card: #1f1f23;
    --yellow: #f0e92a;
    --purple: #6b429c;
    --purple-soft: #8869af;
    --white: #ffffff;
    --ink: #1f1f23;
  }
  * { margin: 0; padding: 0; box-sizing: border-box; }
  html, body {
    width: 1200px; height: 780px; overflow: hidden;
    background: var(--stage);
    font-family: "Open Sans", sans-serif;
  }
  .stage { position: relative; width: 1200px; height: 780px; }
  .card {
    position: absolute; top: 80px;
    width: 360px; height: 620px;
    background: var(--card);
    border-radius: 22px;
    overflow: hidden;
    box-shadow: 0 18px 40px rgba(0,0,0,.55);
  }
  .card--back { left: 170px; }
  .card--front { left: 670px; }

  .back-pattern {
    position: absolute; inset: 0;
    background:
      radial-gradient(circle at 50% 52%, rgba(240,233,42,.85) 0, rgba(240,233,42,.35) 55px, rgba(240,233,42,0) 110px),
      linear-gradient(135deg, #5a5a60 0%, #2a2a2f 35%, #1f1f23 60%, #18181b 100%);
  }

  .brand {
    position: absolute; top: 44px; left: 0; width: 100%;
    display: flex; flex-direction: column; align-items: center; gap: 14px;
  }
  .brand__dot { width: 118px; height: 118px; border-radius: 50%; background: var(--purple); }
  .brand__name {
    font-weight: 600; font-size: 17px; letter-spacing: .04em;
    color: var(--white); text-transform: uppercase;
  }

  .details {
    position: absolute; top: 318px; left: 0; width: 100%;
    text-align: center; color: var(--white);
  }
  .person__name { font-weight: 800; font-size: 30px; line-height: 1.1; }
  .person__first { color: var(--yellow); }
  .person__last { color: var(--purple-soft); }
  .person__role { font-weight: 600; font-size: 14px; margin-top: 4px; }
  .dot-row { display: block; margin: 14px auto 8px; }
  .contact { font-size: 14px; line-height: 1.45; }

  .tagline {
    position: absolute; left: 0; bottom: 34px; width: 100%;
    background: var(--yellow); color: var(--ink);
    font-weight: 600; font-size: 14px; text-align: center;
    padding: 7px 0;
  }
</style>
</head>
<body>
<main class="stage">
  <section class="card card--back">
    <div class="back-pattern" role="img" aria-label="Decorative star pattern with a large yellow star at the centre"></div>
  </section>

  <section class="card card--front">
    <div class="brand">
      <div class="brand__dot"></div>
      <div class="brand__name">Walk Beside The River</div>
    </div>

    <div class="details">
      <div class="person__name"><span class="person__first">Danica</span> <span class="person__last">Hollow</span></div>
      <div class="person__role">CEO/Director</div>

      <svg class="dot-row" width="320" height="28" viewBox="0 0 320 28" aria-hidden="true">
        <g fill="#f0e92a">
          <circle cx="122" cy="14" r="7"/><circle cx="104" cy="14" r="6.5"/><circle cx="87" cy="14" r="6"/>
          <circle cx="71" cy="14" r="5"/><circle cx="57" cy="14" r="4"/><circle cx="45" cy="14" r="3.5"/>
          <circle cx="35" cy="14" r="3"/><circle cx="27" cy="14" r="2.5"/>
          <circle cx="198" cy="14" r="7"/><circle cx="216" cy="14" r="6.5"/><circle cx="233" cy="14" r="6"/>
          <circle cx="249" cy="14" r="5"/><circle cx="263" cy="14" r="4"/><circle cx="275" cy="14" r="3.5"/>
          <circle cx="285" cy="14" r="3"/><circle cx="293" cy="14" r="2.5"/>
          <circle cx="145" cy="14" r="12"/><circle cx="175" cy="14" r="12"/>
        </g>
        <path d="M140 8 q-2 1 0 5 q3 5 7 7 q3 1 4 -1 l-3 -2 l-2 1 q-3 -2 -4 -4 l1 -2 z" fill="#1f1f23"/>
        <rect x="168" y="9" width="14" height="10" rx="1.5" fill="none" stroke="#1f1f23" stroke-width="1.6"/>
        <path d="M168 10 l7 5 l7 -5" fill="none" stroke="#1f1f23" stroke-width="1.6"/>
      </svg>

      <div class="contact">
        <div class="contact__phone">0481 637 092</div>
        <div class="contact__email">walkbesidetheriver@mailcove.com.au</div>
      </div>

      <svg class="dot-row" width="320" height="28" viewBox="0 0 320 28" aria-hidden="true">
        <g fill="#f0e92a">
          <circle cx="137" cy="14" r="7"/><circle cx="119" cy="14" r="6.5"/><circle cx="102" cy="14" r="6"/>
          <circle cx="86" cy="14" r="5"/><circle cx="72" cy="14" r="4"/><circle cx="60" cy="14" r="3.5"/>
          <circle cx="50" cy="14" r="3"/><circle cx="42" cy="14" r="2.5"/>
          <circle cx="183" cy="14" r="7"/><circle cx="201" cy="14" r="6.5"/><circle cx="218" cy="14" r="6"/>
          <circle cx="234" cy="14" r="5"/><circle cx="248" cy="14" r="4"/><circle cx="260" cy="14" r="3.5"/>
          <circle cx="270" cy="14" r="3"/><circle cx="278" cy="14" r="2.5"/>
          <circle cx="160" cy="14" r="12"/>
        </g>
        <path d="M160 22 q-6 -6 -6 -10 a6 6 0 0 1 12 0 q0 4 -6 10 z" fill="#1f1f23"/>
        <circle cx="160" cy="12" r="2.2" fill="#f0e92a"/>
      </svg>

      <div class="contact">
        <div class="contact__address">PO Box 926 Kellerton QLD 4572</div>
      </div>
    </div>

    <div class="tagline">Mental Health Support Rosalind Tavener</div>
  </section>
</main>
</body>
</html>
```